Commercial Real Estate Property Sign

Design a 4' x 4' sign that pops. Refer to examples.

Must include the following information:
A space to list (For Sale, For Lease, Build-to-Suite or Available)
BrightKeel,LLC
Commercial Real Estate
company website
My Name (Marcus Pellow)
My Phone #

Industry/Entity Type

Real Estate

```html
<!DOCTYPE html>
<html lang="en">
<head>
<meta charset="utf-8">
<title>BrightKeel LLC – Commercial Real Estate Sign</title>
<link rel="stylesheet" href="https://fonts.googleapis.com/css2?family=Barlow:wght@400;500;700&display=swap">
<style>
  :root {
    --header-grey: #3a3a3a;
    --panel-black: #1b1b1b;
    --brand-orange: #e8650a;
    --white: #ffffff;
    --ink: #1b1b1b;
  }
  html, body {
    margin: 0;
    padding: 0;
    overflow: hidden;
    background: var(--panel-black);
  }
  .sign {
    position: relative;
    width: 1200px;
    height: 1200px;
    background: var(--panel-black);
    font-family: "Barlow", Arial, sans-serif;
    overflow: hidden;
  }
  .sign-header {
    position: absolute;
    left: 0; top: 0;
    width: 1200px; height: 274px;
    background: var(--header-grey);
  }
  .brand-mark {
    position: absolute;
    left: 38px; top: 53px;
    width: 56px; height: 115px;
    background: #000;
  }
  .brand-name {
    position: absolute;
    left: 0; right: 0; top: 46px;
    text-align: center;
    margin: 0;
    font-size: 104px;
    font-weight: 400;
    line-height: 1.2;
    letter-spacing: 0.12em;
    color: var(--white);
    padding-left: 40px;
  }
  .brand-tagline {
    position: absolute;
    left: 0; right: 0; top: 176px;
    display: flex;
    align-items: center;
    gap: 18px;
    font-size: 44px;
    font-weight: 500;
    color: var(--white);
    line-height: 1.2;
  }
  .brand-tagline .rule {
    flex: 1;
    height: 3px;
    background: var(--brand-orange);
  }
  .agent-name {
    position: absolute;
    left: 0; right: 0; top: 422px;
    margin: 0;
    text-align: center;
    font-size: 90px;
    font-weight: 500;
    color: var(--brand-orange);
    line-height: 1.2;
  }
  .agent-phone {
    position: absolute;
    left: 0; right: 0; top: 540px;
    margin: 0;
    text-align: center;
    font-size: 124px;
    font-weight: 700;
    color: var(--brand-orange);
    line-height: 1.2;
    letter-spacing: 0.02em;
  }
  .listing-band {
    position: absolute;
    left: 0; top: 814px;
    width: 1200px; height: 198px;
    background: var(--brand-orange);
    display: flex;
    align-items: center;
    justify-content: center;
  }
  .listing-status {
    margin: 0;
    font-size: 104px;
    font-weight: 700;
    color: var(--ink);
    line-height: 1;
  }
  .listing-status .initial { color: var(--white); }
  .website {
    position: absolute;
    left: 0; right: 0; top: 1060px;
    display: flex;
    align-items: center;
    justify-content: center;
    gap: 22px;
    font-size: 74px;
    font-weight: 700;
    color: var(--brand-orange);
    line-height: 1.2;
  }
  .website svg { width: 46px; height: 46px; }
</style>
</head>
<body>
  <main class="sign">
    <header class="sign-header">
      <div class="brand-mark"></div>
      <h1 class="brand-name">BrightKeel LLC</h1>
      <div class="brand-tagline">
        <span class="rule"></span>
        <span>Commercial Real Estate</span>
        <span class="rule"></span>
      </div>
    </header>

    <p class="agent-name">Marcus Pellow</p>
    <p class="agent-phone">469.555.0182</p>

    <section class="listing-band">
      <p class="listing-status"><span class="initial">F</span>or Space for <span class="initial">L</span>ease</p>
    </section>

    <div class="website">
      <svg viewBox="0 0 24 24" fill="none" stroke="currentColor" stroke-width="1.6" aria-hidden="true">
        <circle cx="12" cy="12" r="10"/>
        <ellipse cx="12" cy="12" rx="4.5" ry="10"/>
        <line x1="2" y1="12" x2="22" y2="12"/>
        <path d="M4 7h16M4 17h16"/>
      </svg>
      <span>www.mybrightkeel.com</span>
    </div>
  </main>
</body>
</html>
```